Business card for Luxury Portable Restroom Trailer company

We are a Luxury Portable Restroom Trailer Company Called FALCRIDGE HIRES. Based in Orange County California. We provide portable restroom trailers for events, such as, Weddings, Concerts, Charity events, Sporting events, Tournaments, Corporate events, ect. We rent and Sell the Luxury restrooms. Our colors are white, grey, and Orange. As you will see in the logo we uploaded.
There are 2 people in the company so the names and titles will change for the 3 people but card will remain the same. Here is the information for each Person: Dwight Penner CFO 555 318-0476
next Person: Leon Marchetti VP 555 318-0476
Next Person: Owen Marchetti CEO 555 318-0476
Information to include on the card: Luxury Restroom Trailers Rental and Sales. Weddings, Concerts, Charity, Sporting and Corp. Events.

```html
<!DOCTYPE html>
<html lang="en">
<head>
<meta charset="utf-8">
<title>Falcridge Hires – Business Card</title>
<link href="https://fonts.googleapis.com/css2?family=Source+Sans+3:wght@400;700&display=swap" rel="stylesheet">
<style>
  :root {
    --backdrop: #999a99;
    --card: #ffffff;
    --orange: #f26b24;
    --orange-soft: #f58a4e;
    --grey: #58595b;
    --text: #4a4a4c;
  }
  * { margin: 0; padding: 0; box-sizing: border-box; }
  html, body { width: 1200px; height: 1200px; overflow: hidden; }
  body {
    background: var(--backdrop);
    font-family: "Source Sans 3", "Myriad Pro", sans-serif;
    position: relative;
  }
  .card {
    position: absolute;
    left: 232px;
    width: 736px;
    height: 452px;
    background: var(--card);
    border-radius: 40px;
    overflow: hidden;
  }
  .card--front { top: 116px; }
  .card--back { top: 632px; }

  .brand-name {
    position: absolute;
    font-weight: 700;
    letter-spacing: 1px;
    white-space: nowrap;
    line-height: 1;
  }
  .card--front .brand-name {
    left: 36px; top: 66px;
    font-size: 46px;
    color: var(--orange);
  }
  .card--back .brand-name {
    right: 46px; top: 80px;
    font-size: 58px;
    color: var(--grey);
  }

  .accent-bar {
    position: absolute;
    left: 0; top: 248px;
    width: 25px; height: 60px;
    background: var(--orange);
  }
  .person-name {
    position: absolute;
    left: 36px; top: 242px;
    font-size: 35px;
    font-weight: 700;
    color: var(--orange);
    line-height: 1.1;
    white-space: nowrap;
  }
  .contact-line {
    position: absolute;
    left: 36px; top: 284px;
    font-size: 24px;
    color: var(--text);
    white-space: nowrap;
  }
  .contact-line .label { color: var(--orange); }
  .divider {
    position: absolute;
    left: 36px; top: 330px;
    width: 652px; height: 2px;
    background: var(--orange);
  }
  .services {
    position: absolute;
    left: 36px; top: 346px;
    width: 680px;
    font-size: 22px;
    letter-spacing: -0.2px;
    line-height: 29px;
    color: var(--text);
  }

  .mascot-art {
    position: absolute;
    left: 0; top: 200px;
    width: 346px; height: 252px;
    background: linear-gradient(135deg, var(--orange) 0%, var(--orange-soft) 100%);
  }
</style>
</head>
<body>
  <section class="card card--front">
    <div class="brand-name">FALCRIDGE HIRES</div>
    <div class="accent-bar"></div>
    <h1 class="person-name">LEON MARCHETTI VP</h1>
    <p class="contact-line"><span class="label">CONTACT:</span> 555 318-0476</p>
    <div class="divider"></div>
    <p class="services">Luxury Restroom Trailers Rental and Sales. Weddings, Concerts, Charity, Sporting and Corp. Events.</p>
  </section>

  <section class="card card--back">
    <div class="brand-name">FALCRIDGE HIRES</div>
    <div class="mascot-art" role="img" aria-label="Large orange brand mascot artwork"></div>
  </section>
</body>
</html>
```